Wordpress Website Update - Elementor

I'm currently using Elementor and would like my site to be updated. A nice facelift to the current pages. We are a small boutique animation service company.
I have a list of similar production houses to use as references and would like the format/style of the site not to feel so corporate and infuse the fun that we bring to working with clients on animated projects.

Additionally, I'd like to add 2 more pages focusing on more portfolio work and Original IP - which is now our primary goal to sell our show ideas. Maybe have a password projected behind an image showcasing the show/ film. Go to our current site to review. www.pebblemoatfilms.com

Animation/ Commercials/ Vorlica/ Quelbar/ Durno/ KVT - Okay with first page being shorter and not as long as well. Have contact us 'above the fold' on options as well.

Animation and Film

• Current 3 pages - additional 2 - we can focus on layout and arrangement with temporary images then swap with real assets when ready.
• site examples: pirtolstudios.com, Mardle House, Fenra Studios, Gorbleck.net, Quillstone Animation, Brindlemop Animation Studios, ZaZe Studios use Varkel Plus as inspiration.

```html
<!DOCTYPE html>
<html lang="en">
<head>
<meta charset="utf-8">
<title>Pebble Moat Films</title>
<link href="https://fonts.googleapis.com/css2?family=Poppins:wght@400;500;600;700&display=swap" rel="stylesheet">
<style>
:root{
  --purple:#5a2fd0;
  --purple-deep:#5524c4;
  --purple-soft:#7b4fe0;
  --ink:#1d1d2b;
  --body:#3a3a4a;
  --grey-band:#f3f4f6;
  --white:#ffffff;
  --night:#1a1f5c;
}
*{margin:0;padding:0;box-sizing:border-box}
html,body{width:1200px;height:4488px;overflow:hidden}
body{font-family:"Poppins",sans-serif;color:var(--ink);background:var(--white);position:relative}
.abs{position:absolute}
.nav{position:absolute;top:0;left:0;width:1200px;height:86px;z-index:3;border-bottom:1px solid rgba(255,255,255,.15)}
.brand{position:absolute;font-weight:700;color:var(--white);letter-spacing:.5px;line-height:1}
.brand small{display:block;font-size:9px;font-weight:500;letter-spacing:6px;margin-top:5px}
.nav .brand{left:45px;top:22px;font-size:30px}
.menu{position:absolute;display:flex;gap:0;font-size:15px;color:var(--white)}
.menu span{position:absolute;white-space:nowrap}
.icon-btn{position:absolute;top:30px}
.hero{position:absolute;top:0;left:0;width:1200px;height:685px;background:radial-gradient(ellipse at 55% 45%,#3b4bb0 0%,#26307f 40%,#141a4d 80%)}
.hero h1{position:absolute;top:255px;width:100%;text-align:center;font-size:52px;font-weight:600;color:var(--white)}
.hero p{position:absolute;top:333px;width:100%;text-align:center;font-size:20px;color:var(--white)}
.btn{position:absolute;display:flex;align-items:center;justify-content:center;font-size:13px;font-weight:600;letter-spacing:.5px}
.btn-light{background:var(--white);color:var(--purple)}
.btn-solid{background:var(--purple-deep);color:var(--white)}
.feature{position:absolute;left:0;width:1200px}
.eyebrow{position:absolute;font-size:18px;color:var(--ink)}
.title{position:absolute;font-size:32px;font-weight:500;color:var(--purple);text-transform:uppercase}
.copy{position:absolute;font-size:14px;line-height:25.7px;color:var(--body);width:470px}
.more{position:absolute;font-size:13px;font-weight:600;display:flex;align-items:center;gap:12px}
.right{text-align:right}
.media{position:absolute}
.projects{background:var(--purple-deep);top:1658px;height:685px}
.projects .eyebrow,.projects .title{width:100%;text-align:center;color:var(--white)}
.tile{position:absolute;width:276px;height:206px}
.tile-label{position:absolute;left:61px;top:90px;color:var(--white);font-weight:600;font-size:18px}
.skill{position:absolute;width:264px;height:264px;border-radius:50%;border:3px solid var(--purple);background:var(--white);text-align:center}
.skill.active{border:none;background:linear-gradient(135deg,#6a3ce0,#8f5cec)}
.skill .glyph{position:absolute;left:102px;top:28px;width:60px;height:66px;border-radius:14px;background:#e7e0fa}
.skill.active .glyph{background:rgba(255,255,255,.35)}
.skill h3{position:absolute;top:136px;width:100%;font-size:22px;font-weight:500;color:var(--purple)}
.skill p{position:absolute;top:172px;left:30px;width:204px;font-size:14px;line-height:25px;color:var(--body)}
.skill.active h3,.skill.active p{color:var(--white)}
.cta{position:absolute;top:3166px;left:0;width:1200px;height:514px;background:radial-gradient(ellipse at 50% 55%,#6a4fc9 0%,#3d2a8a 45%,#1d1840 85%)}
.cta-panel{position:absolute;top:0;left:601px;width:599px;height:87px;background:var(--white)}
.cta h2{position:absolute;font-size:30px;font-weight:500}
.rule{position:absolute;height:3px}
.footer{position:absolute;top:4165px;left:0;width:1200px;height:323px;background:linear-gradient(180deg,#5a2cd0,#6a3ce0)}
.footer .brand{left:0;width:100%;text-align:center;top:82px;font-size:40px}
.social{position:absolute;top:4406px;width:38px;height:38px;border-radius:50%;background:var(--white)}
</style>
</head>
<body>

<section class="hero" role="img" aria-label="Moonlit fantasy harbour with a ship and castle, in deep blues"></section>

<header class="nav">
  <div class="brand">Pebble Moat<small>FILMS</small></div>
  <nav class="menu" style="left:0;top:33px">
    <span style="left:392px">Home</span>
    <span style="left:471px">About</span>
    <span style="left:550px">Projects ⌄</span>
    <span style="left:644px">Expertise</span>
    <span style="left:745px">Contact</span>
  </nav>
  <svg class="icon-btn" style="left:1054px" width="26" height="26" viewBox="0 0 26 26" fill="none" stroke="#fff" stroke-width="2.4"><circle cx="11" cy="11" r="8"/><line x1="17" y1="17" x2="24" y2="24"/></svg>
  <svg class="icon-btn" style="left:1112px;top:32px" width="30" height="22" viewBox="0 0 30 22" stroke="#fff" stroke-width="2.6"><line x1="0" y1="2" x2="30" y2="2"/><line x1="0" y1="11" x2="30" y2="11"/><line x1="0" y1="20" x2="30" y2="20"/></svg>
</header>

<div class="hero" style="background:none;z-index:2">
  <h1>Pebble Moat Films</h1>
  <p>Cooking up incredible home-grown stories that</p>
  <div class="btn btn-light" style="left:516px;top:378px;width:168px;height:42px">ABOUT US</div>
</div>

<section class="feature" style="top:685px;height:486px">
  <div class="eyebrow right" style="right:639px;top:103px">Animation Is Where Pmf Thrives</div>
  <div class="title right" style="right:639px;top:144px">Animation Reel</div>
  <p class="copy right" style="right:639px;top:211px">Lorem Ipsum Dolor Sit Amet, Consectetur Adipiscing Elit, Sed Do Eiusmod Tempor Incididunt Ut Labore Et Dolore Magna Aliqua. Ut Enim Ad Minim Veniam, Quis Nostrud Exercitation Ullamco Laboris Nisi Ut Aliquip Ex Ea Commodo Consequat. Duis Aute Irure Dolor In Reprehenderit In Voluptate</p>
  <div class="more" style="right:636px;top:366px">LEARN MORE
    <svg width="26" height="12" viewBox="0 0 26 12" fill="none" stroke="#1d1d2b" stroke-width="1.8"><line x1="0" y1="6" x2="24" y2="6"/><polyline points="19,1 24,6 19,11"/></svg></div>
  <div class="media" role="img" aria-label="Two animated girls in a colourful classroom" style="left:617px;top:90px;width:473px;height:305px;background:linear-gradient(135deg,#3f8fc0,#e0667a 60%,#d84f8c)"></div>
</section>

<section class="feature" style="top:1171px;height:487px;background:var(--grey-band)">
  <div class="media" role="img" aria-label="Animated puppy in a safari outfit" style="left:108px;top:92px;width:475px;height:305px;background:linear-gradient(135deg,#3c4f8f,#c9a46a 55%,#6d4d2c)"></div>
  <div class="eyebrow" style="left:627px;top:104px">Fresh Out The Render Oven</div>
  <div class="title" style="left:627px;top:146px">Giraffes &amp; Kids Are Free</div>
  <p class="copy" style="left:627px;top:212px">Lorem Ipsum Dolor Sit Amet, Consectetur Adipiscing Elit, Sed Do Eiusmod Tempor Incididunt Ut Labore Et Dolore Magna Aliqua. Ut Enim Ad Minim Veniam, Quis Nostrud Exercitation Ullamco Laboris Nisi Ut Aliquip Ex Ea Commodo Consequat. Duis Aute Irure Dolor In Reprehenderit In Voluptate</p>
  <div class="more" style="left:627px;top:367px">LEARN MORE
    <svg width="26" height="12" viewBox="0 0 26 12" fill="none" stroke="#1d1d2b" stroke-width="1.8"><line x1="0" y1="6" x2="24" y2="6"/><polyline points="19,1 24,6 19,11"/></svg></div>
</section>

<section class="feature projects">
  <div class="eyebrow" style="top:72px">Just A Few.</div>
  <div class="title" style="top:106px">Projects</div>
  <div class="tile" role="img" aria-label="Animated scientist beside a speaker" style="left:19px;top:166px;background:linear-gradient(135deg,#4a3a30,#8a7a6a)"><span class="tile-label">Are Experience</span></div>
  <div class="tile" role="img" aria-label="Animated town street with palm trees" style="left:315px;top:166px;background:linear-gradient(180deg,#bcd6ee,#8aa36a)"></div>
  <div class="tile" role="img" aria-label="Underwater scene with divers and fish" style="left:611px;top:166px;background:linear-gradient(135deg,#1f5fb0,#3a9ad8)"></div>
  <div class="tile" role="img" aria-label="Animated scientist beside a presenter" style="left:907px;top:166px;background:linear-gradient(135deg,#9a9590,#5a4a40)"></div>
  <div class="tile" role="img" aria-label="Animated scientist at a desk with a cloud sign" style="left:19px;top:390px;background:linear-gradient(135deg,#8ec8ea,#e9eef3)"></div>
  <div class="tile" role="img" aria-label="Animated elf beside a slot game screen" style="left:315px;top:390px;background:linear-gradient(135deg,#3f7a3a,#b8332c)"></div>
  <div class="tile" role="img" aria-label="Wooden signpost in a forest scene" style="left:611px;top:390px;background:linear-gradient(135deg,#3d6b3a,#8a5a34)"></div>
  <div class="tile" role="img" aria-label="Blue character model sheet" style="left:907px;top:390px;background:linear-gradient(135deg,#ffffff,#6aa8d8 60%,#1a1a22)"></div>
</section>

<section class="feature" style="top:2343px;height:823px">
  <div class="eyebrow" style="width:100%;text-align:center;top:80px">Creative Experts That Solve Problems</div>
  <div class="title" style="width:100%;text-align:center;top:118px">Our Expertise</div>
  <div class="skill active" style="left:143px;top:180px"><div class="glyph" role="img" aria-label="Creature icon"></div><h3>Ip Creation</h3><p>Developing, Directing and Selling captivating</p></div>
  <div class="skill" style="left:457px;top:180px"><div class="glyph" role="img" aria-label="Creature icon"></div><h3>Story</h3><p>Developing, Directing and Selling captivating</p></div>
  <div class="skill" style="left:767px;top:180px"><div class="glyph" role="img" aria-label="Creature icon"></div><h3>Animation</h3><p>Developing, Directing and Selling captivating</p></div>
  <div class="skill" style="left:143px;top:471px"><div class="glyph" role="img" aria-label="Creature icon"></div><h3>3d Rigging</h3><p>Developing, Directing and Selling captivating</p></div>
  <div class="skill" style="left:457px;top:471px"><div class="glyph" role="img" aria-label="Creature icon"></div><h3>Character Design</h3><p>Developing, Directing and Selling captivating</p></div>
  <div class="skill" style="left:767px;top:471px"><div class="glyph" role="img" aria-label="Creature icon"></div><h3>Vis Dev</h3><p>Developing, Directing and Selling captivating</p></div>
</section>

<section class="cta" role="img" aria-label="Animated characters and a puppy in purple light">
  <div class="cta-panel"></div>
  <h2 style="left:44px;top:20px;width:505px;text-align:center;color:var(--white)">Why Wait Let's Co-Create!</h2>
  <div class="rule" style="left:44px;top:67px;width:505px;background:var(--white)"></div>
  <h2 style="left:643px;top:20px;width:505px;text-align:center;color:var(--ink)">Achieve More With A Grin!</h2>
  <div class="rule" style="left:643px;top:67px;width:505px;background:var(--purple)"></div>
  <div class="abs" style="top:248px;width:100%;text-align:center;font-size:20px;font-weight:500;color:var(--white)">When Is NOW A Good Time To Write?</div>
  <div class="btn btn-solid" style="left:516px;top:297px;width:167px;height:42px">CONTACT US</div>
</section>

<section class="feature" style="top:3680px;height:485px">
  <div class="eyebrow right" style="right:639px;top:104px">The Sky's The Limit</div>
  <div class="title right" style="right:639px;top:146px">We Make It Fun</div>
  <p class="copy right" style="right:639px;top:210px">Did we mention we LOVE what we do? The industry has changed a lot over the years. And yes there's a lot of outsourcing nowadays and you get what you pay for. So I can guarantee you get the best when you work with us. We cut the fluff and get down to business making sure it's</p>
  <div class="more" style="right:636px;top:366px">LEARN MORE
    <svg width="26" height="12" viewBox="0 0 26 12" fill="none" stroke="#1d1d2b" stroke-width="1.8"><line x1="0" y1="6" x2="24" y2="6"/><polyline points="19,1 24,6 19,11"/></svg></div>
  <div class="media" role="img" aria-label="Artist working on a 3D character at a desk" style="left:617px;top:90px;width:473px;height:306px;background:linear-gradient(135deg,#c9c0b4,#6a4a3a 55%,#2a2a40)"></div>
</section>

<footer class="footer">
  <div class="brand">Pebble Moat<small style="font-size:10px;letter-spacing:9px">FILMS</small></div>
  <nav class="menu" style="left:0;top:172px">
    <span style="left:392px">Home</span>
    <span style="left:471px">About</span>
    <span style="left:550px">Projects</span>
    <span style="left:644px">Expertise</span>
    <span style="left:745px">Contact</span>
  </nav>
  <div class="rule" style="left:640px;top:205px;width:72px;height:2px;background:var(--white)"></div>
  <div class="abs" style="left:108px;top:250px;font-size:14px;color:var(--white)">Copyright © 2022 Pebble Moat Films. All rights reserved.</div>
</footer>
<div class="social" style="left:962px"></div>
<div class="social" style="left:1007px"></div>
<div class="social" style="left:1051px"></div>

</body>
</html>
```